I need a business card designed using the logo provided either vertical or horizontal......Harbourline Property Group is an Australian based real estate company that caters for the upper end of the market so the design of the business card "must reflect" the companies image!!
Colour combinations are optional but "must be realistic" and must be able to be accurately useable CMYK colours.
Please consider that any colours used "must be able to be used" and be suitable in following designs for "pull out banner signs" and "real estate signs".
The colours and the font in the attached designs are for example and other combinations are encouraged.
Target Market(s)
The High End of the Australian real estate market
Industry/Entity Type
Business
Contact Information for Business Card
Logo - Business Name - Director + Licensed Real Estate Agent - Mobile Number (Cell Phone) - Business Number - Fax - Email Address - Web address
Requirements
Must have
- Designs and colours (CMYK) that can easily be interpreted by an Australian printer.
Nice to have
- Some alternative ideas on colour and font..........the ones provided are ok and have been provided as an example but I am looking for alternative ideas
Should not have
- Loud, overly bright colours. Designs that do not reflect the professional standards of the business.
- Designs that look good on a computer monitor but can not be re-created on a printing press.............this is most important when it comes to shading etc.

```html
<!DOCTYPE html>
<html lang="en">
<head>
<meta charset="utf-8">
<title>Harbourline Property Group – Business Card</title>
<link href="https://fonts.googleapis.com/css2?family=Roboto+Condensed:wght@400;500;700&display=swap" rel="stylesheet">
<style>
  :root {
    --bg: #e7e3dc;
    --paper: #f7f7f5;
    --gold: #b08a2e;
    --gold-light: #c9a24a;
    --ink: #232323;
    --brand-grey: #3b3b3b;
    --white: #ffffff;
  }
  * { margin: 0; padding: 0; box-sizing: border-box; }
  html, body {
    width: 1200px; height: 892px; overflow: hidden;
    background: var(--bg);
    font-family: "Roboto Condensed", Arial, sans-serif;
  }
  .canvas {
    width: 1200px; height: 892px;
    display: flex; align-items: center; justify-content: center; gap: 48px;
  }
  .card {
    position: relative; width: 520px; height: 297px;
    background: var(--ink);
    box-shadow: 0 10px 28px rgba(0,0,0,.18);
    overflow: hidden;
  }
  .card__shapes { position: absolute; inset: 0; }
  .brand {
    position: absolute; left: 26px; top: 96px; width: 170px;
    display: flex; align-items: flex-start; gap: 10px;
  }
  .brand__mark { width: 14px; height: 14px; background: var(--gold); flex: none; margin-top: 4px; }
  .brand__name {
    color: var(--brand-grey); font-weight: 500; font-size: 20px;
    line-height: 1.1; letter-spacing: .5px; text-transform: uppercase;
  }
  .card--back .brand { top: 100px; width: 190px; }
  .card--back .brand__name { font-size: 22px; }

  .identity {
    position: absolute; right: 22px; top: 18px; text-align: right; color: var(--white);
  }
  .identity__company { font-size: 15px; font-weight: 500; letter-spacing: 1.5px; text-transform: uppercase; }
  .identity__person { font-size: 26px; font-weight: 700; margin-top: 12px; line-height: 1; }
  .identity__role { font-size: 12px; letter-spacing: .5px; margin-top: 4px; }

  .contacts {
    position: absolute; color: var(--white); list-style: none;
    font-size: 14.5px; line-height: 1.45;
  }
  .card--front .contacts { right: 22px; bottom: 22px; text-align: right; }
  .contacts li { display: flex; align-items: center; justify-content: flex-end; gap: 8px; }
  .contacts svg { width: 11px; height: 11px; fill: var(--gold-light); flex: none; }
  .contacts .no-icon { padding-right: 19px; }
  .card--back .contacts { right: 26px; bottom: 24px; font-size: 17px; line-height: 1.35; text-align: right; }
  .card--back .contacts li { justify-content: flex-end; }
</style>
</head>
<body>
<main class="canvas">

  <section class="card card--front" aria-label="Business card front">
    <svg class="card__shapes" viewBox="0 0 520 297" preserveAspectRatio="none" aria-hidden="true">
      <polygon points="200,0 520,0 520,122 272,160" fill="var(--gold)"/>
      <polygon points="0,0 200,0 272,160 150,297 0,297" fill="var(--paper)"/>
    </svg>

    <div class="brand">
      <span class="brand__mark"></span>
      <span class="brand__name">Harbourline Property Group</span>
    </div>

    <div class="identity">
      <p class="identity__company">Harbourline Property Group</p>
      <p class="identity__person">Employee name</p>
      <p class="identity__role">Managing Director</p>
    </div>

    <ul class="contacts">
      <li>455-3120 8840
        <svg viewBox="0 0 24 24"><path d="M6.6 10.8a15.2 15.2 0 0 0 6.6 6.6l2.2-2.2c.3-.3.7-.4 1-.2 1.1.4 2.3.6 3.6.6.6 0 1 .4 1 1V20c0 .6-.4 1-1 1A17 17 0 0 1 3 4c0-.6.4-1 1-1h3.5c.6 0 1 .4 1 1 0 1.3.2 2.5.6 3.6.1.3 0 .7-.2 1z"/></svg>
      </li>
      <li>info@harbourlinegroup.com
        <svg viewBox="0 0 24 24"><path d="M2 5h20v14H2zm2 2v.5l8 5 8-5V7l-8 5z"/></svg>
      </li>
      <li>www.harbourlinegroup.com
        <svg viewBox="0 0 24 24"><path d="M12 2a10 10 0 1 0 0 20 10 10 0 0 0 0-20zm6.9 6h-3a15 15 0 0 0-1.3-3.9A8 8 0 0 1 18.9 8zM12 4c.8 1.1 1.5 2.5 1.9 4h-3.8c.4-1.5 1.1-2.9 1.9-4zM4.3 14a8 8 0 0 1 0-4h3.4a16 16 0 0 0 0 4zm.8 2h3a15 15 0 0 0 1.3 3.9A8 8 0 0 1 5.1 16zm3-8h-3a8 8 0 0 1 4.3-3.9A15 15 0 0 0 8.1 8zM12 20c-.8-1.1-1.5-2.5-1.9-4h3.8c-.4 1.5-1.1 2.9-1.9 4zm2.3-6H9.7a14 14 0 0 1 0-4h4.6a14 14 0 0 1 0 4zm.3 5.9a15 15 0 0 0 1.3-3.9h3a8 8 0 0 1-4.3 3.9zm1.7-5.9a16 16 0 0 0 0-4h3.4a8 8 0 0 1 0 4z"/></svg>
      </li>
      <li>14 Wharf Terrace Suite 2
        <svg viewBox="0 0 24 24"><path d="M12 2a7 7 0 0 0-7 7c0 5 7 13 7 13s7-8 7-13a7 7 0 0 0-7-7zm0 9.5a2.5 2.5 0 1 1 0-5 2.5 2.5 0 0 1 0 5z"/></svg>
      </li>
      <li class="no-icon">Sydney, NSW 2000</li>
    </ul>
  </section>

  <section class="card card--back" aria-label="Business card back">
    <svg class="card__shapes" viewBox="0 0 520 297" preserveAspectRatio="none" aria-hidden="true">
      <polygon points="240,0 520,0 520,60 300,160" fill="var(--gold)"/>
      <polygon points="0,0 240,0 300,160 170,297 0,297" fill="var(--paper)"/>
    </svg>

    <div class="brand">
      <span class="brand__mark"></span>
      <span class="brand__name">Harbourline Property Group</span>
    </div>

    <ul class="contacts">
      <li>455-3120 8840</li>
      <li>info@harbourlinegroup.com</li>
      <li>www.harbourlinegroup.com</li>
      <li>14 Wharf Terrace Suite 2</li>
      <li>Sydney, NSW 2000</li>
    </ul>
  </section>

</main>
</body>
</html>
```